I work in creative/artistic projects across different mediums.
It needs to communicate creativity, style, sexy, uniqueness, individuality and sophistication.
It should not look corporate.
Colours I like are black silver gold deep purple, chocolate, orchid.
It doesn't have to make use of all these colours.
I do not like bright primary colors.
Updates

Project Deadline Extended
Reason: Still in the communication process and to allow the person enough time to finish the design. Though i should know in the next day or two. Thank you.

Target Market(s)

creatives and companies wanting to inject creativity into thier business.

Industry/Entity Type

Work

Contact Information for Business Card

Corwin Haldley
0418592036
corwin@corwinhaldley-example.com

quietgoldenhourstudio.example.au

Requirements
Should not have
• Anything corporate OR OLD FASHIONED

```html
<!DOCTYPE html>
<html lang="en">
<head>
<meta charset="utf-8">
<title>Corwin Haldley — Business Card</title>
<link rel="stylesheet" href="https://fonts.googleapis.com/css2?family=Mulish:wght@700;800&display=swap">
<style>
  :root {
    --page-bg: #f2f5f6;
    --card-black: #000000;
    --chocolate: #80532f;
    --cocoa: #a87a52;
    --caramel: #c4976a;
    --band-shadow: #2a2522;
    --deep-purple: #3d2a6e;
    --ink-white: #ffffff;
  }
  * { margin: 0; padding: 0; box-sizing: border-box; }
  html, body {
    width: 1200px;
    height: 761px;
    overflow: hidden;
    background: var(--page-bg);
  }
  .canvas {
    position: relative;
    width: 1200px;
    height: 761px;
  }
  .business-card {
    position: absolute;
    left: 310px;
    top: 271px;
    width: 584px;
    height: 351px;
    display: block;
  }
  .card-text {
    font-family: "Mulish", "Century Gothic", sans-serif;
    font-weight: 700;
    fill: var(--ink-white);
  }
  .contact-phone { font-size: 17px; }
  .contact-email { font-size: 14px; }
  .contact-web { font-size: 15px; }
  .card-name {
    font-family: "Mulish", "Century Gothic", sans-serif;
    font-weight: 800;
    font-size: 35px;
    fill: var(--caramel);
  }
</style>
</head>
<body>
<main class="canvas">
  <svg class="business-card" viewBox="0 0 584 351" xmlns="http://www.w3.org/2000/svg" aria-label="Business card for Corwin Haldley">
    <defs>
      <clipPath id="card-clip"><rect width="584" height="351"/></clipPath>
      <radialGradient id="flourish-glow" cx="0.55" cy="0.5" r="0.6">
        <stop offset="0" stop-color="#2a1f45"/>
        <stop offset="0.6" stop-color="#120c20"/>
        <stop offset="1" stop-color="#000000"/>
      </radialGradient>
      <radialGradient id="swirl-glow" cx="0.5" cy="0.5" r="0.5">
        <stop offset="0" stop-color="#9a6a42"/>
        <stop offset="1" stop-color="#80532f" stop-opacity="0"/>
      </radialGradient>
      <path id="arc-phone" d="M44 178 A178 178 0 0 0 222 0"/>
      <path id="arc-email" d="M44 243 A243 243 0 0 0 287 0"/>
      <path id="arc-web" d="M44 308 A308 308 0 0 0 352 0"/>
    </defs>

    <g clip-path="url(#card-clip)">
      <rect class="card-base" width="584" height="351" fill="var(--card-black)"/>

      <rect class="flourish-area" x="240" y="20" width="344" height="331" fill="url(#flourish-glow)"
            role="img" aria-label="Deep purple and white flowing flourish swirls"/>

      <g class="arc-bands">
        <circle cx="44" cy="3" r="340" fill="var(--band-shadow)"/>
        <circle cx="44" cy="0" r="340" fill="var(--caramel)"/>
        <circle cx="44" cy="3" r="262" fill="var(--band-shadow)"/>
        <circle cx="44" cy="0" r="262" fill="var(--cocoa)"/>
        <circle cx="44" cy="3" r="204" fill="var(--band-shadow)"/>
        <circle cx="44" cy="0" r="204" fill="var(--chocolate)"/>
      </g>

      <ellipse class="swirl-area" cx="90" cy="65" rx="90" ry="80" fill="url(#swirl-glow)"
               role="img" aria-label="Faint tan spiral swirl ornament"/>

      <g class="contact-icons" fill="var(--ink-white)">
        <path class="icon-phone" d="M53 146 q6 -4 9 0 l4 8 q1 4 -3 6 l-3 2 q2 8 10 14 l3 -2 q4 -3 6 1 l5 7 q2 4 -2 7 q-5 4 -11 2 q-16 -7 -21 -27 q-2 -12 3 -18 z"/>
        <g class="icon-mail">
          <rect x="47" y="214" width="34" height="24" rx="1"/>
          <path d="M48 215 L64 229 L80 215" fill="none" stroke="var(--cocoa)" stroke-width="2"/>
          <path d="M48 237 L60 226 M80 237 L68 226" fill="none" stroke="var(--cocoa)" stroke-width="1.5"/>
        </g>
        <g class="icon-web">
          <circle cx="66" cy="298" r="17"/>
          <path d="M49 293 H83 M49 303 H83 M66 281 V315" stroke="var(--caramel)" stroke-width="1.5" fill="none"/>
          <ellipse cx="66" cy="298" rx="8" ry="17" fill="none" stroke="var(--caramel)" stroke-width="1.5"/>
          <rect x="50" y="294" width="32" height="8" fill="var(--ink-white)"/>
          <text x="66" y="301.5" text-anchor="middle" font-family="Mulish, sans-serif" font-weight="800" font-size="8" fill="var(--caramel)">www</text>
        </g>
      </g>

      <text class="card-text contact-phone">
        <textPath href="#arc-phone" startOffset="79">0418 592 036</textPath>
      </text>
      <text class="card-text contact-email">
        <textPath href="#arc-email" startOffset="59">corwin@corwinhaldley-example.com</textPath>
      </text>
      <text class="card-text contact-web">
        <textPath href="#arc-web" startOffset="77">www.quietgoldenhourstudio.example.au</textPath>
      </text>

      <text class="card-name" x="238" y="307">Corwin Haldley</text>
    </g>
  </svg>
</main>
</body>
</html>
```